Letterhead and matching envelope design for a dental office

We need a new stationary design, letterhead and envelope #10, for a dental office in Denver area. We are called Bright Harbor Dental. We want a simple and minimalistic design but not a boring design. I wish to have one good point that makes it look professional. I have attached our logo. Feel free to use either one. I want the design for letterhead and envelope look like a "matching pair" but not look the same. The envelope doesn't have to be white and it will have an address window on bottom left.

Target Market(s)

everyone who visits dentist (adults)

Industry/Entity Type

Dental

Font styles to use
Other font styles liked:
• close to font on logo or something that matches well

Requirements
Must have
• professional
• simple, minimalistic
• unique point that stands out
Nice to have
• matching but not same design for letterhead and envelope
Should not have
• not look like all the other boring designs
• no flowery, distracting feats

```html
<!DOCTYPE html>
<html lang="en">
<head>
<meta charset="utf-8">
<title>Bright Harbor Dental – Envelope #10</title>
<link rel="stylesheet" href="https://fonts.googleapis.com/css2?family=PT+Sans:wght@400;700&display=swap">
<style>
  :root {
    --green: #3bb54a;
    --green-soft: #9fd3a6;
    --green-pale: #d6eed9;
    --paper: #ffffff;
    --backdrop: #e6e6e6;
    --ink-light: #ffffff;
  }
  * { margin: 0; padding: 0; box-sizing: border-box; }
  html, body {
    width: 1200px; height: 795px; overflow: hidden;
    background: var(--backdrop);
    font-family: "PT Sans", Arial, sans-serif;
  }
  .canvas { position: relative; width: 1200px; height: 795px; }
  .envelope {
    position: absolute; width: 800px; height: 347px;
    background: var(--paper);
    box-shadow: 0 2px 6px rgba(0,0,0,.12);
  }
  .envelope svg { position: absolute; inset: 0; width: 100%; height: 100%; }
  .envelope--back { left: 340px; top: 28px; }
  .envelope--front { left: 60px; top: 420px; }

  .brand-name {
    position: absolute;
    font-weight: 700;
    text-transform: uppercase;
    letter-spacing: .22em;
    white-space: nowrap;
    text-align: center;
    line-height: 1.25;
  }
  .envelope--front .brand-name {
    left: 330px; top: 95px; width: 220px;
    font-size: 17px; color: var(--green);
  }
  .envelope--back .brand-name {
    left: 320px; top: 128px; width: 160px;
    font-size: 12px; color: var(--ink-light);
  }

  .contact-list {
    position: absolute; left: 24px; top: 140px;
    list-style: none; color: var(--ink-light);
    font-size: 13px; line-height: 21px;
  }
  .contact-list li { display: flex; align-items: center; gap: 8px; white-space: nowrap; }
  .contact-icon {
    width: 14px; height: 14px; border-radius: 50%;
    background: var(--ink-light);
    display: inline-flex; align-items: center; justify-content: center;
    flex: none;
  }
  .contact-icon svg { position: static; width: 9px; height: 9px; }
</style>
</head>
<body>
<main class="canvas">

  <section class="envelope envelope--back" aria-label="Envelope back">
    <svg viewBox="0 0 800 347" aria-hidden="true">
      <path fill="var(--green)" d="M0,0 L800,0 L800,290 Q800,338 752,324 L450,232 Q400,216 350,204 L0,24 Z"/>
    </svg>
    <div class="brand-name">Bright Harbor<br>Dental</div>
  </section>

  <section class="envelope envelope--front" aria-label="Envelope front">
    <svg viewBox="0 0 800 347" aria-hidden="true">
      <path fill="none" stroke="var(--green-pale)" stroke-width="10" d="M80,100 C280,96 400,130 505,218 C590,288 670,305 800,306"/>
      <path fill="none" stroke="var(--green-soft)" stroke-width="6" d="M40,108 C250,100 380,140 488,228 C575,298 665,313 800,316"/>
      <path fill="var(--green)" d="M0,118 C220,108 360,150 470,240 C560,310 660,322 800,326 L800,347 L0,347 Z"/>
    </svg>

    <div class="brand-name">Bright Harbor<br>Dental</div>

    <ul class="contact-list">
      <li>
        <span class="contact-icon"><svg viewBox="0 0 10 10"><path fill="var(--green)" d="M2,1 L4,1 L4.6,3 L3.5,3.8 Q4.3,5.7 6.2,6.5 L7,5.4 L9,6 L9,8 Q9,9 8,9 Q1,8.5 1,2 Q1,1 2,1 Z"/></svg></span>
        720-555-0148
      </li>
      <li>
        <span class="contact-icon"><svg viewBox="0 0 10 10"><rect x="1" y="2.5" width="8" height="5.5" fill="var(--green)"/><path d="M1.3,2.8 L5,5.6 L8.7,2.8" stroke="#fff" stroke-width=".8" fill="none"/></svg></span>
        info@brightharbordental.com
      </li>
      <li>
        <span class="contact-icon"><svg viewBox="0 0 10 10"><circle cx="5" cy="5" r="3.8" fill="none" stroke="var(--green)" stroke-width="1"/><path d="M1.2,5 H8.8 M5,1.2 V8.8" stroke="var(--green)" stroke-width=".8"/></svg></span>
        www.brightharbordental.com
      </li>
      <li>
        <span class="contact-icon"><svg viewBox="0 0 10 10"><path fill="var(--green)" d="M5,0.8 A3,3 0 0 1 8,3.8 C8,6 5,9.2 5,9.2 C5,9.2 2,6 2,3.8 A3,3 0 0 1 5,0.8 Z"/><circle cx="5" cy="3.8" r="1.1" fill="#fff"/></svg></span>
        2215 Meadow Ridge Dr, Suite 210 Arvada, CO 80004
      </li>
    </ul>
  </section>

</main>
</body>
</html>
```